Business Card Design Competition

We need a business card design for our Internet Marketing company. We require both front and back designs and the final card must be 89x53mm in size, plus crop marks to 91x55mm. Colours as per logo, plus perhaps black and/or grey (#828282).
Final text must be editable (if you can supply an editable Fireworks PNG, even better)...
FRONT TEXT:
Full Name
Position
Address Line
Suburb, State, Postcode
Phone: 0000 000 000
Mobile: 0000 000 000
Email: xxx@brightlanemedia.com.au
Web: www.brightlanemedia.com.au
Rear of card should be a fresh design plus our slogan text: "Getting You Noticed" in large font, then in small text "Kestrel Holdings Pty Ltd (ABN: 42 561 903 774)".
Target Market(s)
Small/Medium Businesses
Industry/Entity Type
Business

```html
<!DOCTYPE html>
<html lang="en">
<head>
<meta charset="utf-8">
<title>Brightlane Media – Business Card</title>
<link rel="stylesheet" href="https://fonts.googleapis.com/css2?family=Carlito:wght@400;700&display=swap">
<style>
  :root {
    --page: #ffffff;
    --card: #ffffff;
    --card-edge: #9a9a9a;
    --band: #c9e19c;
    --band-line: #b3d37a;
    --orange: #f7941d;
    --green: #8dc63f;
    --grey: #828282;
    --ink: #111111;
  }
  html, body {
    margin: 0;
    padding: 0;
    width: 970px;
    height: 1200px;
    overflow: hidden;
    background: var(--page);
  }
  .canvas {
    position: relative;
    width: 970px;
    height: 1200px;
    font-family: "Carlito", "Calibri", sans-serif;
  }
  .card {
    position: absolute;
    left: 6px;
    width: 954px;
    background: var(--card);
    border: 2px solid var(--card-edge);
    border-radius: 34px;
    overflow: hidden;
    box-shadow: 0 3px 6px rgba(0, 0, 0, 0.18);
  }
  .card--front { top: 6px; height: 570px; }
  .card--back { top: 600px; height: 582px; }

  .band {
    position: absolute;
    left: 0;
    right: 0;
    bottom: 0;
    height: 58px;
    background: var(--band);
    border-top: 2px solid var(--band-line);
    box-sizing: border-box;
  }

  .brand {
    position: absolute;
    left: 48px;
    top: 118px;
    display: flex;
    align-items: center;
    gap: 40px;
  }
  .brand__dot {
    width: 290px;
    height: 290px;
    border-radius: 50%;
    background: var(--orange);
    flex: none;
  }
  .brand__name {
    font-weight: 700;
    color: var(--orange);
    font-size: 120px;
    line-height: 1.0;
    margin: 0;
  }

  .contact {
    position: absolute;
    left: 95px;
    top: 86px;
    margin: 0;
    font-style: normal;
    font-size: 33px;
    line-height: 33px;
    color: var(--ink);
  }
  .contact__group { margin: 0 0 44px; }
  .contact__group:last-child { margin-bottom: 0; }
  .contact__group p { margin: 0; }

  .slogan {
    position: absolute;
    right: 44px;
    top: 96px;
    margin: 0;
    text-align: right;
    font-weight: 700;
    font-size: 54px;
    line-height: 1.05;
    color: var(--green);
  }
  .legal {
    position: absolute;
    right: 44px;
    bottom: 0;
    height: 58px;
    margin: 0;
    display: flex;
    align-items: center;
    font-size: 18px;
    color: var(--grey);
  }
</style>
</head>
<body>
<main class="canvas">
  <section class="card card--front" aria-label="Card front">
    <div class="brand">
      <span class="brand__dot" aria-hidden="true"></span>
      <h1 class="brand__name">Brightlane<br>Media</h1>
    </div>
    <div class="band"></div>
  </section>

  <section class="card card--back" aria-label="Card back">
    <address class="contact">
      <div class="contact__group">
        <p>Full Name</p>
        <p>Position</p>
      </div>
      <div class="contact__group">
        <p>Address Line</p>
        <p>Suburb, State, Postcode</p>
      </div>
      <div class="contact__group">
        <p>Phone: 0000 000 000</p>
        <p>Mobile: 0000 000 000</p>
      </div>
      <div class="contact__group">
        <p>Email: xxx@brightlanemedia.com.au</p>
        <p>Web: www.brightlanemedia.com.au</p>
      </div>
    </address>
    <p class="slogan">Getting<br>You<br>Noticed</p>
    <div class="band"></div>
    <p class="legal">Kestrel Holdings Pty Ltd (ABN: 42 561 903 774)</p>
  </section>
</main>
</body>
</html>
```